New Business Card Design Project

I need a design for business cards, i am an electrical business called "Corvane Electrical and Communications" i need the cards to be double sided with the company logo on the back (attached) the front needs to say my company name, web site, email address, telephone number, and ABN number and electrical license number. I am open to different arrangements of the information but would like the background to be incorporating something electrical or something that looks smart. open to all additional ideas also.

The company colours are orange and grey see logo attached.

Business Name: Corvane Electrical and Communications
Website: corvaneelectricalandcomms.example.com.au
Email: brent@corvaneelectricalandcomms.example.com.au
Telephone(mobile): 0481209736
ABN: 71208349162
Lic No: 418273D

Target Market(s)

Business entities, Project Managers, Accounts, Clients

Industry/Entity Type

Electrician

Contact Information for Business Card

I need a design for business cards, i am an electrical business called "Corvane Electrical and Communications" i need the cards to be double sided with the company logo on the back (attached) the front needs to say my company name

Font styles to use
Serif
Sans Serif

Colors
f37122
5c5c5c

Requirements
Must have
• Must have the Logo on the back open to different ways of it being on the back but had in mind to keep it central but again open to other options
Nice to have
• A real modern cool background that is eye catching yet contemporary
Should not have
• No backgrounds of a light bulb or plug or anything like that

```html
<!DOCTYPE html>
<html lang="en">
<head>
<meta charset="utf-8">
<title>Corvane Electrical and Communications – Business Cards</title>
<link href="https://fonts.googleapis.com/css2?family=Open+Sans:wght@400;600&display=swap" rel="stylesheet">
<style>
  :root {
    --page-bg: #2b2b2b;
    --card-black: #050505;
    --navy-deep: #060a18;
    --navy-mid: #0f1c3a;
    --teal-glow: #1d4f5c;
    --orange: #f7a823;
    --white: #ffffff;
    --soft-white: #e8e8e8;
  }
  * { margin: 0; padding: 0; box-sizing: border-box; }
  html, body { width: 1200px; height: 900px; overflow: hidden; }
  body {
    background: var(--page-bg);
    font-family: "Open Sans", Arial, sans-serif;
    position: relative;
  }
  .card {
    position: absolute;
    width: 640px;
    height: 366px;
    border-radius: 22px;
    overflow: hidden;
    box-shadow: 0 14px 30px rgba(0,0,0,0.45);
  }
  /* Back side: logo */
  .card-back {
    left: 120px; top: 70px;
    background: var(--card-black);
  }
  .card-back .wordmark {
    position: absolute;
    left: 0; right: 0; top: 96px;
    text-align: center;
  }
  .wordmark-dot {
    display: inline-block;
    width: 16px; height: 16px;
    border-radius: 50%;
    background: var(--orange);
    vertical-align: middle;
    margin-right: 14px;
  }
  .wordmark-name {
    color: var(--white);
    font-weight: 400;
    font-size: 66px;
    letter-spacing: 6px;
    vertical-align: middle;
    line-height: 1;
  }
  .wordmark-sub {
    display: block;
    color: var(--white);
    font-weight: 400;
    font-size: 17px;
    letter-spacing: 3px;
    margin-top: 10px;
  }
  .card-back .web {
    position: absolute;
    left: 0; right: 0; bottom: 54px;
    text-align: center;
    font-size: 15px;
    font-weight: 600;
    color: var(--white);
  }
  .card-back .web .domain { color: var(--orange); }

  /* Front side: details */
  .card-front {
    left: 440px; top: 464px;
    background: var(--navy-deep);
  }
  .light-field {
    position: absolute; inset: 0;
    background:
      radial-gradient(ellipse 60% 45% at 55% 60%, var(--teal-glow) 0%, transparent 70%),
      radial-gradient(ellipse 80% 60% at 40% 55%, var(--navy-mid) 0%, transparent 75%),
      var(--navy-deep);
  }
  .front-logo {
    position: absolute;
    left: 30px; top: 176px;
    width: 270px;
  }
  .front-logo .wordmark-dot { width: 10px; height: 10px; margin-right: 8px; }
  .front-logo .wordmark-name { font-size: 40px; letter-spacing: 3px; }
  .front-logo .wordmark-sub { font-size: 10.5px; letter-spacing: 1.4px; margin-top: 6px; }
  .divider {
    position: absolute;
    left: 318px; top: 92px;
    width: 1.5px; height: 178px;
    background: var(--orange);
  }
  .details {
    position: absolute;
    left: 334px; top: 86px;
    color: var(--soft-white);
  }
  .person-name {
    color: var(--orange);
    font-size: 23px;
    font-weight: 400;
    letter-spacing: 0.5px;
    line-height: 1.1;
  }
  .person-role {
    font-size: 12px;
    font-weight: 600;
    margin-bottom: 10px;
  }
  .contact-list { list-style: none; font-size: 11.5px; }
  .contact-list li { display: flex; align-items: center; height: 19px; }
  .contact-list svg { width: 11px; height: 11px; margin-right: 8px; flex: none; }
  .reg-line { font-size: 12px; margin-top: 8px; }
  .reg-line .label { color: var(--orange); }
</style>
</head>
<body>

<section class="card card-back" aria-label="Card back">
  <div class="wordmark">
    <span class="wordmark-dot"></span><span class="wordmark-name">CORVANE</span>
    <span class="wordmark-sub">ELECTRICAL &amp; COMMUNICATIONS</span>
  </div>
  <p class="web">www.<span class="domain">corvaneelectricalandcomms</span>.example.com.au</p>
</section>

<section class="card card-front" aria-label="Card front">
  <div class="light-field" role="img" aria-label="Abstract glowing blue and teal light streaks on dark navy"></div>

  <div class="front-logo">
    <span class="wordmark-dot"></span><span class="wordmark-name">CORVANE</span>
    <span class="wordmark-sub">ELECTRICAL &amp; COMMUNICATIONS</span>
  </div>

  <div class="divider"></div>

  <div class="details">
    <h1 class="person-name">MARLO TENNANT</h1>
    <p class="person-role">DIRECTOR</p>
    <ul class="contact-list">
      <li>
        <svg viewBox="0 0 12 12" aria-hidden="true"><path d="M2.5 1 L4.5 1 L5.2 3.6 L4 4.6 Q5 7 7.4 8 L8.4 6.8 L11 7.5 L11 9.5 Q11 11 9.5 11 Q1 10 1 2.5 Q1 1 2.5 1 Z" fill="var(--orange)"/></svg>
        0481-209-736
      </li>
      <li>
        <svg viewBox="0 0 12 12" aria-hidden="true"><rect x="1" y="2.5" width="10" height="7" fill="none" stroke="var(--orange)" stroke-width="1.3"/><path d="M1 2.5 L6 6.5 L11 2.5" fill="none" stroke="var(--orange)" stroke-width="1.3"/></svg>
        brent@corvaneelectricalandcomms.example.com.au
      </li>
      <li>
        <svg viewBox="0 0 12 12" aria-hidden="true"><circle cx="6" cy="6" r="5" fill="none" stroke="var(--orange)" stroke-width="1.2"/><ellipse cx="6" cy="6" rx="2.2" ry="5" fill="none" stroke="var(--orange)" stroke-width="1"/><path d="M1 6 H11" stroke="var(--orange)" stroke-width="1"/></svg>
        www.corvaneelectricalandcomms.example.com.au
      </li>
    </ul>
    <p class="reg-line"><span class="label">ABN:</span> 71208349162</p>
    <p class="reg-line"><span class="label">Lic No:</span> 418273D</p>
  </div>
</section>

</body>
</html>
```